Business Cards Design for the electrical wholesaler: clean bold dynamic :)

We need a business card design that would follow our latest brand guidelines. As an electrical wholesaler we want to bring a fresh look and feel into the industry. The design should be clean bold and dynamic. It should come alive with the renewed energy of our green colour. Our grey colour should keep things balanced and complement the notion of maturity and responsibility. We employ Lato as a corporate font however are not bound by this font and we’re open to interpretation here.

Target Market(s)

Electrical contractors

Industry/Entity Type

Business

Contact Information for Business Card

Logo
Name & Surname: Halyna Dorosh
Job Title: Director of Marketing
Email: halya.dorosh@quillmail.example
Cell phone: XXX.XXX.XXXX
Address: 20517 - 87 Ave. Edmonton, AB, Canada. T6K 4N8
Business Phone: 780.555.0184
Website: www.brovix.example

Font styles to use
Other font styles liked:
• Lato

Requirements
Must have
• Logo & website
Nice to have
• Brand elements - some of them you may find in the attached Brand Guidelines (e.g. three lines on the background signifying "W")

```html
<!DOCTYPE html>
<html lang="en">
<head>
<meta charset="utf-8">
<title>Brovix Business Cards</title>
<link href="https://fonts.googleapis.com/css2?family=Lato:wght@400;700&display=swap" rel="stylesheet">
<style>
  :root {
    --bg: #d3e7ee;
    --paper: #ffffff;
    --green: #8cc043;
    --green-dark: #5f8a27;
    --grey: #4f5153;
    --ink: #2e2f31;
  }
  * { box-sizing: border-box; margin: 0; padding: 0; }
  html, body { width: 1200px; height: 900px; overflow: hidden; }
  body {
    background: var(--bg);
    font-family: "Lato", Arial, sans-serif;
    color: var(--ink);
    position: relative;
  }
  .card {
    position: absolute;
    width: 560px;
    height: 320px;
    background: var(--paper);
    border-radius: 16px;
    overflow: hidden;
    box-shadow: 0 6px 18px rgba(40, 60, 70, 0.25);
  }
  .card--front { left: 50px; top: 90px; }
  .card--back { left: 590px; top: 480px; }

  .brand { display: flex; align-items: center; gap: 12px; }
  .brand__dot { width: 22px; height: 22px; border-radius: 50%; background: var(--green); }
  .brand__name { font-weight: 700; color: var(--grey); letter-spacing: 1px; }

  .card--front .brand {
    position: absolute; left: 0; right: 0; top: 110px; justify-content: center;
  }
  .card--front .brand__name { font-size: 64px; line-height: 1; }
  .card--front .brand__dot { width: 34px; height: 34px; }
  .front__web {
    position: absolute; left: 0; right: 0; bottom: 38px;
    text-align: center; font-size: 15px; color: var(--ink);
  }

  .back__panel {
    position: absolute; inset: 0;
    background: var(--grey);
    clip-path: polygon(48% 0, 100% 0, 100% 100%, 64% 100%);
  }
  .card--back .brand { position: absolute; left: 30px; top: 34px; }
  .card--back .brand__name { font-size: 42px; line-height: 1; }

  .ribbon {
    position: absolute; left: 44%; top: 34px; width: 230px; height: 58px;
    background: var(--green); color: #fff;
    padding: 10px 0 0 36px;
  }
  .ribbon__fold {
    position: absolute; left: 44%; top: 92px; width: 0; height: 0;
    border-top: 14px solid var(--green-dark);
    border-left: 22px solid transparent;
  }
  .ribbon__name { font-size: 18px; font-weight: 700; line-height: 1.1; }
  .ribbon__role { font-size: 12px; line-height: 1.4; }

  .address {
    position: absolute; right: 26px; top: 170px; width: 200px;
    text-align: center; color: #fff; font-size: 13px; line-height: 1.4;
  }
  .address svg { display: block; margin: 0 auto 8px; }

  .contacts {
    position: absolute; left: 30px; bottom: 26px; list-style: none;
  }
  .contacts li {
    display: flex; align-items: center; gap: 10px;
    font-size: 14px; height: 26px;
  }
  .contacts .icon {
    width: 20px; height: 20px; background: var(--green);
    display: flex; align-items: center; justify-content: center;
  }
</style>
</head>
<body>

<section class="card card--front">
  <div class="brand">
    <span class="brand__dot"></span>
    <span class="brand__name">brovix</span>
  </div>
  <p class="front__web">www.brovix.example</p>
</section>

<section class="card card--back">
  <div class="back__panel"></div>

  <div class="brand">
    <span class="brand__dot"></span>
    <span class="brand__name">brovix</span>
  </div>

  <div class="ribbon">
    <p class="ribbon__name">Halyna Dorosh</p>
    <p class="ribbon__role">Director of Marketing</p>
  </div>
  <div class="ribbon__fold"></div>

  <div class="address">
    <svg width="12" height="16" viewBox="0 0 12 16"><path d="M6 0a6 6 0 0 1 6 6c0 4-6 10-6 10S0 10 0 6a6 6 0 0 1 6-6z" fill="#fff"/><circle cx="6" cy="6" r="2.2" fill="#4f5153"/></svg>
    20517 - 87 Ave. Edmonton, AB,<br>Canada. T6K 4N8
  </div>

  <ul class="contacts">
    <li><span class="icon"><svg width="12" height="12" viewBox="0 0 12 12"><path d="M2 1l2 0 1 3-1.5 1a7 7 0 0 0 3.5 3.5L8 7l3 1v2a1 1 0 0 1-1 1A9 9 0 0 1 1 2a1 1 0 0 1 1-1z" fill="#fff"/></svg></span>780-555-0127</li>
    <li><span class="icon"><svg width="12" height="12" viewBox="0 0 12 12"><rect x="1" y="4" width="10" height="7" rx="1" fill="none" stroke="#fff"/><path d="M2 4V2h8v2" fill="none" stroke="#fff"/><circle cx="6" cy="7.5" r="1.5" fill="#fff"/></svg></span>780-555-0184</li>
    <li><span class="icon"><svg width="12" height="12" viewBox="0 0 12 12"><rect x="1" y="2.5" width="10" height="7" fill="none" stroke="#fff"/><path d="M1 2.5l5 4 5-4" fill="none" stroke="#fff"/></svg></span>halya.dorosh@quillmail.example</li>
    <li><span class="icon"><svg width="12" height="12" viewBox="0 0 12 12"><circle cx="6" cy="6" r="4.8" fill="none" stroke="#fff"/><path d="M1.2 6h9.6M6 1.2c-2 2.5-2 7.1 0 9.6M6 1.2c2 2.5 2 7.1 0 9.6" fill="none" stroke="#fff" stroke-width=".8"/></svg></span>www.brovix.example</li>
  </ul>
</section>

</body>
</html>
```